Label design for organic saffron, saffron and herbal syrup

We cultivate saffron, Damszen roses, flowers and herbs. We would need a recognizable outfit (label) for our products. Theoretically (and practically) we have "converted" the family coat of arms into a kind of LOGO. I would send this in the attachment. It would be nice if - in one way or another - this LOGO / coat of arms could be used (certainly with other colors). For some time we have played with the idea of changing the second part of the family name "Wallmoser" (in German .... greuth sounds similar to Kraut / herb [English]) .... eg Wallmoser's saffron syrup into the labeling.
Our products are primarily syrups, currently herbal syrup and saffron syrup. Here the first problem arises, the only bottles / caps that are actually approved for syrup filling (hot filling) are appallingly ugly (see attachment), the only possibility of "sprucing up" is to use so-called "shrink sleeves" (here we need a diameter of 31 and a length of about 40), the colors of which are also limited. Besides the syrup, we sell saffron as a spice and various herbal mixtures (see appendix current packaging saffron). Our quantities are small (syrup 200ml-330ml), saffron in the gram range.
We also need quasi the back of the labeling (this should be able to be redefined per charge) .... Batch 1 (with small quantity has eg more of herb xy than the next batch or the saffron syrup with batch xy needs more / less saffron). In addition, we are certified organic (for this reason, the reverse side would also have to contain all the requirements of organic labeling) [see attachment].
We do not really want to address a specific clientele. Maybe just people who want to taste, enjoy, mix drinks, cook .... (and - unfortunately - don't like Corvel syrup :-) and want to pay a bit more, or find our saffron or herbs better than others) .
In summary
- Strong recognition value (possibly inclusion of "coat of arms", color variable ... although I personally don't like yellow that much)
- Saffron syrup (the color of the saffron syrup is yellow / golden-yellow-light orange, in a transparent ugly bottle)
- Herbal syrup (color variable from blue / green / brown / red elements, in transparent ugly bottle)
Saffron and other herbs (very small containers, type of container not yet fixed)
Regarding a potential "style" I can unfortunately give little information. On the one hand, I am in love with minimalism, on the other hand, I find the translucent, cryptic, implied enormously attractive and sometimes even the "overloaded" colorful has its charm. I think that all in all, it just has to be coherent, and then it will be good.
Requirements
Must have
- Integration of Code of Arms, modifiable for different products

```html
<!DOCTYPE html>
<html lang="en">
<head>
<meta charset="utf-8">
<title>Wallmoser Herbal Sirup Label</title>
<link rel="stylesheet" href="https://fonts.googleapis.com/css2?family=Cormorant+Garamond:wght@600&family=Open+Sans:wdth,wght@75..100,700&display=swap">
<style>
  :root {
    --forest: #0b4226;
    --forest-dark: #07321c;
    --gold: #d4a83c;
    --gold-light: #f1d27a;
    --gold-dark: #a67c1e;
    --cream: #fdf0c8;
    --ink: #2b2a2a;
    --indigo: #2d2a6e;
    --badge-green: #c6e0a1;
    --badge-border: #7fae49;
    --white: #ffffff;
  }
  html, body {
    margin: 0;
    padding: 0;
    width: 784px;
    height: 1200px;
    overflow: hidden;
    background: var(--white);
  }
  .canvas {
    position: relative;
    width: 784px;
    height: 1200px;
    overflow: hidden;
    background: var(--white);
  }
  .label {
    position: absolute;
    left: 45px;
    top: 43px;
    width: 701px;
    height: 1112px;
    background: var(--cream);
  }
  .ornament-band {
    position: absolute;
    left: 45px;
    top: 43px;
    width: 701px;
    height: 355px;
    background:
      radial-gradient(circle at 12% 30%, rgba(212,168,60,0.45), transparent 32%),
      radial-gradient(circle at 88% 30%, rgba(212,168,60,0.45), transparent 32%),
      radial-gradient(circle at 15% 85%, rgba(212,168,60,0.3), transparent 30%),
      radial-gradient(circle at 85% 85%, rgba(212,168,60,0.3), transparent 30%),
      linear-gradient(180deg, var(--forest) 0%, var(--forest-dark) 100%);
  }
  .shapes {
    position: absolute;
    left: 0;
    top: 0;
  }
  .brand-mark {
    position: absolute;
    left: 342px;
    top: 190px;
    width: 100px;
    height: 100px;
    border: 3px solid var(--indigo);
    border-radius: 50%;
    box-sizing: border-box;
  }
  .brand-name {
    position: absolute;
    left: 232px;
    top: 305px;
    width: 320px;
    text-align: center;
    font-family: "Cormorant Garamond", serif;
    font-weight: 600;
    font-size: 54px;
    line-height: 1;
    color: var(--indigo);
  }
  .product-title {
    position: absolute;
    left: 238px;
    top: 515px;
    width: 311px;
    margin: 0;
    text-align: center;
    font-family: "Cormorant Garamond", serif;
    font-weight: 600;
    font-size: 62px;
    line-height: 72px;
    color: var(--white);
    letter-spacing: 1px;
  }
  .rotated {
    position: absolute;
    transform: rotate(-90deg);
    transform-origin: center center;
    font-family: "Open Sans", sans-serif;
    font-weight: 700;
    font-stretch: 85%;
    color: var(--ink);
    letter-spacing: 0.6px;
  }
  .ingredients {
    left: -207px;
    top: 744px;
    width: 645px;
    height: 72px;
    margin: 0;
    font-size: 13.5px;
    line-height: 18px;
    text-align: center;
  }
  .producer {
    left: 478px;
    top: 630px;
    width: 400px;
    height: 76px;
    font-size: 13.5px;
    line-height: 19px;
    text-align: right;
  }
  .producer p { margin: 0; }
  .producer .organic-note { margin-bottom: 12px; }
  .best-before-box {
    position: absolute;
    left: 642px;
    top: 923px;
    width: 83px;
    height: 186px;
    background: var(--white);
  }
  .best-before {
    left: 597px;
    top: 1047px;
    width: 110px;
    height: 24px;
    font-size: 17px;
    line-height: 24px;
    letter-spacing: 1.5px;
  }
  .volume, .ratio {
    position: absolute;
    top: 1082px;
    font-family: "Open Sans", sans-serif;
    font-weight: 700;
    font-stretch: 85%;
    font-size: 21px;
    line-height: 26px;
    color: var(--ink);
  }
  .volume { left: 254px; }
  .ratio { left: 462px; }
  .organic-badge {
    position: absolute;
    left: 348px;
    top: 938px;
    width: 92px;
    height: 172px;
    background: var(--badge-green);
    border: 1px solid var(--badge-border);
    box-sizing: border-box;
  }
  .organic-badge .seal-round {
    position: absolute;
    left: 8px;
    top: 8px;
    width: 74px;
    height: 74px;
    background: var(--white);
    border: 3px solid var(--badge-border);
    border-radius: 50%;
    box-sizing: border-box;
  }
  .organic-badge .seal-square {
    position: absolute;
    left: 8px;
    top: 90px;
    width: 74px;
    height: 58px;
    background: #6aa83a;
  }
</style>
</head>
<body>
<div class="canvas">
  <div class="label"></div>

  <div class="ornament-band" role="img" aria-label="Gold mandala ornament pattern on deep green"></div>

  <svg class="shapes" width="784" height="1200" viewBox="0 0 784 1200" aria-hidden="true">
    <defs>
      <linearGradient id="goldBar" x1="0" y1="0" x2="0" y2="1">
        <stop offset="0" stop-color="#f1d27a"/>
        <stop offset="0.5" stop-color="#d4a83c"/>
        <stop offset="1" stop-color="#a67c1e"/>
      </linearGradient>
    </defs>
    <!-- bottle-shaped window in the top band -->
    <path d="M335,43 H451 V125 A172,172 0 0 1 523,398 H261 A172,172 0 0 1 335,125 Z"
          fill="#ffffff" stroke="#d4a83c" stroke-width="4"/>
    <!-- gold divider bar -->
    <rect x="45" y="398" width="701" height="26" fill="url(#goldBar)"/>
    <!-- title tab -->
    <path d="M238,424 V618 A155.5,155.5 0 0 0 549,618 V424 Z"
          fill="#0b4226" stroke="#d4a83c" stroke-width="4"/>
  </svg>

  <div class="brand-mark" aria-hidden="true"></div>
  <div class="brand-name">Wallmoser</div>

  <h1 class="product-title">Herbal<br>Sirup</h1>

  <p class="rotated ingredients">ZUTATEN: Lorem ipsum dolor sit amet, consectetur adipiscing elit. Morbi ultricies molestie orci. Aenean purus mauris, sodales nec diam dignissim, porttitor laoreet enim. Aliquam id sollicitudin turpis. Vivamus aliquet elit sem, et ornare ex aliquam in.</p>

  <div class="rotated producer">
    <p class="organic-note">*aus kontrolliert biologischer Landwirtschaft</p>
    <p>Expertly crafted by: Hallbrunn-Wallmoser</p>
    <p>1234 Street Name, Any City, District, Country</p>
  </div>

  <div class="organic-badge" role="img" aria-label="Organic certification seals">
    <span class="seal-round"></span>
    <span class="seal-square"></span>
  </div>

  <div class="volume">300mL</div>
  <div class="ratio">1:7</div>

  <div class="best-before-box"></div>
  <div class="rotated best-before">Best Before:</div>
</div>
</body>
</html>
```